Maplecrest Disability - Social Security Disability Attorneys

Our company is expanding to attract clients nationwide for our social security disability practice. We have a logo, but I am looking for a creative and elegant letterhead that projects an image of being technologically advanced but still professional enough for the legal field. I am looking for the "wow factor" combined with this is still professional enough for a law practice.

Requesting letterhead and business card design
Updates

Had to update and change the logo. The previous logo had a typo. Please send updates with the new logo for consideration. The letterhead and business cards should be professional enough to be used for a law firm. Thanks.

Industry/Entity Type

Law Practice, Law Firm, Healthcare Industry, Government

Colors

Designer to choose colors to be used in the design.

Requirements
Nice to have
• **Please create a vertical design for the business card**

```html
<!DOCTYPE html>
<html lang="en">
<head>
<meta charset="utf-8">
<title>Maplecrest Disability – Business Card</title>
<link rel="stylesheet" href="https://fonts.googleapis.com/css2?family=Figtree:wght@400;500;700&display=swap">
<style>
  :root {
    --backdrop: #219ed9;
    --card-dark: #181719;
    --card-front-top: #1b1a1c;
    --card-front-bottom: #262527;
    --brand-blue: #4f63b0;
    --brand-orange: #f5862e;
    --text-light: #ffffff;
  }
  * { margin: 0; padding: 0; box-sizing: border-box; }
  html, body {
    width: 1200px; height: 1128px; overflow: hidden;
    background: var(--backdrop);
    font-family: "Figtree", sans-serif;
  }
  .canvas { position: relative; width: 1200px; height: 1128px; }
  .card {
    position: absolute; top: 129px; height: 870px;
    border-radius: 42px; overflow: hidden;
    color: var(--text-light);
  }
  .card--front {
    left: 69px; width: 502px;
    background: linear-gradient(160deg, var(--card-front-top) 30%, var(--card-front-bottom) 75%, var(--card-front-top));
  }
  .card--back { left: 633px; width: 496px; background: var(--card-dark); }
  .line {
    position: absolute; left: 0; right: 0;
    text-align: center; line-height: 1; white-space: nowrap;
  }
  .brand-dot {
    position: absolute; left: 50%; width: 16px; height: 16px;
    margin-left: -8px; border-radius: 50%; background: var(--brand-orange);
  }
  .brand-name {
    color: var(--brand-blue); font-weight: 500; letter-spacing: 2px;
    text-transform: uppercase;
  }
  .brand-tagline {
    color: var(--brand-blue); font-weight: 500; letter-spacing: 2.4px;
    text-transform: uppercase; font-size: 8.5px;
  }
  .card--front .brand-dot { top: 386px; }
  .card--front .brand-name { top: 301px; font-size: 24px; }
  .card--front .brand-tagline { top: 332px; }
  .scan-note { top: 572px; font-size: 16px; font-weight: 500; }
  .industries { font-size: 20px; font-weight: 500; }
  .industries--first { top: 705px; }
  .industries--second { top: 736px; }

  .card--back .brand-dot { top: 113px; }
  .card--back .brand-name { top: 155px; font-size: 26px; }
  .card--back .brand-tagline { top: 188px; }
  .person-name { top: 375px; font-size: 29px; font-weight: 700; }
  .person-role {
    top: 411px; font-size: 22px; font-weight: 400;
    display: flex; justify-content: center; align-items: center; gap: 6px;
  }
  .person-role::before, .person-role::after {
    content: ""; width: 66px; height: 1.5px; background: var(--text-light);
  }
  .address { font-size: 20px; }
  .address--first { top: 547px; }
  .address--second { top: 576px; }
  .contact-icons {
    position: absolute; top: 638px; left: 0; right: 0;
    display: flex; justify-content: center; gap: 35px;
  }
  .contact-icons svg { width: 20px; height: 20px; fill: var(--brand-orange); }
  .contact { font-size: 20px; }
  .contact--phone { top: 686px; }
  .contact--email { top: 718px; }
  .contact--web { top: 750px; }
  .accent-band { position: absolute; left: 0; bottom: 0; width: 100%; height: 20px; }
</style>
</head>
<body>
<main class="canvas">
  <section class="card card--front" aria-label="Business card front">
    <span class="brand-dot" aria-hidden="true" style="top:262px"></span>
    <p class="line brand-name">Maplecrest Disability</p>
    <p class="line brand-tagline">Social Security Disability Attorneys</p>
    <p class="line scan-note">Scan Me To Visit Our Site</p>
    <p class="line industries industries--first">Law Practice, Law Firm,</p>
    <p class="line industries industries--second">Healthcare Industry, Government</p>
  </section>

  <section class="card card--back" aria-label="Business card back">
    <span class="brand-dot" aria-hidden="true"></span>
    <p class="line brand-name">Maplecrest Disability</p>
    <p class="line brand-tagline">Social Security Disability Attorneys</p>
    <p class="line person-name">DANIEL WHITFORD</p>
    <p class="line person-role">Co-Founder</p>
    <p class="line address address--first">Suite 8, Level 14, Wattle</p>
    <p class="line address address--second">Street Sydney NSW 2000</p>
    <div class="contact-icons" aria-hidden="true">
      <svg viewBox="0 0 24 24"><path d="M6.6 10.8a15.1 15.1 0 0 0 6.6 6.6l2.2-2.2a1 1 0 0 1 1-.25 11.4 11.4 0 0 0 3.6.57 1 1 0 0 1 1 1V20a1 1 0 0 1-1 1A17 17 0 0 1 3 4a1 1 0 0 1 1-1h3.5a1 1 0 0 1 1 1c0 1.25.2 2.45.57 3.57a1 1 0 0 1-.25 1z"/></svg>
      <svg viewBox="0 0 24 24"><path d="M2 5h20v14H2z M3.5 6.5 12 13l8.5-6.5" fill="var(--brand-orange)" stroke="var(--card-dark)" stroke-width="1.4"/></svg>
      <svg viewBox="0 0 24 24"><circle cx="12" cy="12" r="10"/><path d="M7 7c2 1 2 3 4 3s1 3 3 3-1 4 1 5M15 4c-1 2 1 3 3 3" fill="none" stroke="var(--card-dark)" stroke-width="1.4"/></svg>
    </div>
    <p class="line contact contact--phone">555-214-7390</p>
    <p class="line contact contact--email">Info@maplecrestdisability.com</p>
    <p class="line contact contact--web">www.maplecrestdisability.com</p>
    <svg class="accent-band" viewBox="0 0 496 20" preserveAspectRatio="none" aria-hidden="true">
      <polygon points="0,0 256,0 232,20 0,20" fill="var(--brand-orange)"/>
      <polygon points="260,0 496,0 496,20 236,20" fill="var(--brand-blue)"/>
    </svg>
  </section>
</main>
</body>
</html>
```